International Business Development Firm, in need of Branded Stationery material

We just made our Logo and now we are looking for branded stationery for our company such as:

* A Letterhead with our company's name, address, and logo at the top in Word format for easy editing
* A more formal letter format with a light background design (watermark) featuring our logo, allowing us to write over it for various documents and presentations
* Business card + Envelopes are a plus but not a must
* PowerPoint for company and product introductions
* An Info sheet with Bullet Points

The design should be professional.
Please ensure the design is high quality and print ready.

Target Market(s)

Businesses and high net value individuels

Industry/Entity Type

International Business Development Firm

Colors

Designer to choose colors to be used in the design.

Requirements
Must have
• word docs so i can use the stationery templates afterwards

```html
<!DOCTYPE html>
<html lang="en">
<head>
<meta charset="utf-8">
<title>Orchid Bridge Stationery</title>
<link rel="stylesheet" href="https://fonts.googleapis.com/css2?family=Lato:wght@400;700&family=Montserrat:wght@600&display=swap">
<style>
  :root {
    --brand: #6b3d8f;
    --brand-soft: #9a7bb4;
    --ink: #222222;
    --paper: #ffffff;
    --backdrop: #f3f3f5;
    --rule: #6b3d8f;
  }
  * { box-sizing: border-box; margin: 0; padding: 0; }
  html, body { width: 1200px; height: 824px; overflow: hidden; background: var(--backdrop); }
  body { position: relative; font-family: "Lato", sans-serif; color: var(--ink); }

  .sheet { position: absolute; background: var(--paper); }
  .wordmark { font-family: "Montserrat", sans-serif; font-weight: 600; color: var(--brand); letter-spacing: 0.5px; white-space: nowrap; display: flex; align-items: center; gap: 6px; }
  .wordmark .dot { display: inline-block; background: var(--brand); }
  .wordmark.on-dark { color: var(--paper); }
  .wordmark.on-dark .dot { background: var(--paper); }

  /* Letterhead */
  .letterhead { left: 127px; top: 100px; width: 442px; height: 625px; }
  .letterhead .wordmark { position: absolute; left: 22px; top: 36px; font-size: 22px; }
  .letterhead .wordmark .dot { width: 12px; height: 12px; }
  .contact { position: absolute; left: 313px; top: 26px; border-left: 1px solid var(--rule); padding-left: 11px; font-size: 8.4px; line-height: 10px; }
  .contact .gap { height: 5px; }
  .contact .row { display: flex; align-items: center; gap: 4px; }
  .contact svg { width: 6px; height: 6px; fill: var(--brand); flex: none; }
  .letter { position: absolute; left: 22px; top: 143px; width: 399px; font-size: 8.8px; line-height: 10px; }
  .letter p { margin-bottom: 11px; }
  .letter .body p { text-align: justify; margin-bottom: 10px; }
  .letter .salute { font-size: 11px; font-weight: 700; margin: 12px 0 13px; }
  .letter .regards { margin-top: 22px; }
  .signature { width: 94px; height: 22px; margin-top: 44px; background: linear-gradient(90deg, #e8e8ea, #f4f4f6); }

  /* Business card front */
  .card-front { left: 633px; top: 100px; width: 213px; height: 122px; border-radius: 8px; }
  .card-front .wordmark { position: absolute; left: 8px; top: 17px; font-size: 13px; gap: 4px; }
  .card-front .wordmark .dot { width: 7px; height: 7px; }
  .person { position: absolute; right: 4px; top: 18px; text-align: right; border-right: 3px solid var(--brand); padding-right: 4px; }
  .person .name { font-weight: 700; color: var(--brand); font-size: 8px; line-height: 9px; }
  .person .role { color: var(--brand-soft); font-size: 5.6px; letter-spacing: 0.2px; }
  .card-contact { position: absolute; left: 8px; top: 68px; font-size: 5.6px; line-height: 7.6px; }
  .card-contact .gap { height: 9px; }
  .card-contact .row { display: flex; align-items: center; gap: 3px; }
  .card-contact svg { width: 4px; height: 4px; fill: var(--brand); }

  /* Business card back */
  .card-back { left: 862px; top: 100px; width: 212px; height: 122px; border-radius: 8px; background: var(--brand); display: flex; align-items: center; justify-content: center; }
  .card-back .wordmark { font-size: 19px; }
  .card-back .wordmark .dot { width: 10px; height: 10px; }

  /* Envelope back */
  .envelope-back { left: 623px; top: 278px; width: 452px; height: 198px; }
  .flap { position: absolute; left: 0; top: 0; width: 100%; height: 59px; background: var(--brand); border-radius: 0 0 40px 40px; }
  .flap .mark { position: absolute; left: 220px; top: 23px; width: 12px; height: 12px; background: var(--paper); }

  /* Envelope front */
  .envelope-front { left: 623px; top: 530px; width: 451px; height: 195px; }
  .envelope-front .wordmark { position: absolute; left: 24px; top: 28px; font-size: 20px; }
  .envelope-front .wordmark .dot { width: 11px; height: 11px; }
  .return-address { position: absolute; left: 68px; top: 69px; font-size: 7.2px; line-height: 10.5px; text-align: center; }
  .window { position: absolute; left: 23px; top: 130px; width: 92px; height: 36px; background: linear-gradient(135deg, #d8d8d8 0%, #d8d8d8 38%, #8e8e8e 55%, #eeeeec 70%, #f0f0ee 100%); }
</style>
</head>
<body>

  <section class="sheet letterhead">
    <div class="wordmark"><span class="dot"></span>ORCHID BRIDGE</div>
    <div class="contact">
      <div>Your address, City</div>
      <div>State, Zip 1234</div>
      <div class="gap"></div>
      <div class="row"><svg viewBox="0 0 10 10"><path d="M2 0l2 2-1 2 3 3 2-1 2 2-2 2C4 10 0 6 0 2z"/></svg>123 456 789</div>
      <div class="row"><svg viewBox="0 0 10 10"><path d="M0 2h10v6H0z"/></svg>info@yourgmail.com</div>
      <div class="row"><svg viewBox="0 0 10 10"><circle cx="5" cy="5" r="5"/></svg>www.yourwebsite.com</div>
    </div>

    <div class="letter">
      <p>January-03-2020</p>
      <p>Mr, Peter Lannom<br>President</p>
      <p>Harbor Crest Group<br>123 Street Name, Suite# 10<br>City, State, 120023</p>
      <p class="salute">Dear Mr, Peter</p>
      <div class="body">
        <p>Lorem ipsum dolor sit amet, consectetur adipiscing elit, sed do eiusmod tempor incididunt ut labore et dolore magna aliqua. Ut enim ad minim veniam, quis nostrud exercitation ullamco laboris nisi ut aliquip ex ea commodo consequat. Duis aute irure dolor in reprehenderit in voluptate velit esse cillum dolore eu fugiat nulla pariatur.</p>
        <p>Lorem ipsum dolor sit amet, consectetur adipiscing elit, sed do eiusmod tempor incididunt ut labore et dolore magna aliqua. Ut enim ad minim veniam, quis nostrud exercitation ullamco laboris nisi ut aliquip ex ea commodo consequat. Duis aute irure dolor in reprehenderit in voluptate velit esse cillum dolore eu fugiat nulla pariatur.</p>
        <p>Lorem ipsum dolor sit amet, consectetur adipiscing elit, sed do eiusmod tempor incididunt ut labore et dolore magna aliqua. Ut enim ad minim veniam, quis nostrud exercitation ullamco laboris nisi ut aliquip ex ea commodo consequat.</p>
        <p>Excepteur sint occaecat cupidatat non proident, sunt in culpa qui officia deserunt mollit anim id est laborum. re et dolore magnam aliquam quaerat voluptatem.</p>
      </div>
      <p class="regards">Regards</p>
      <div class="signature" role="img" aria-label="Handwritten signature of Adrian Kole"></div>
    </div>
  </section>

  <section class="sheet card-front">
    <div class="wordmark"><span class="dot"></span>ORCHID BRIDGE</div>
    <div class="person">
      <div class="name">DANIEL VERNE</div>
      <div class="role">MANAGING DIRECTOR</div>
    </div>
    <div class="card-contact">
      <div>Your address, City</div>
      <div>State, Zip 1234</div>
      <div class="gap"></div>
      <div class="row"><svg viewBox="0 0 10 10"><path d="M2 0l2 2-1 2 3 3 2-1 2 2-2 2C4 10 0 6 0 2z"/></svg>123 456 789</div>
      <div class="row"><svg viewBox="0 0 10 10"><path d="M0 2h10v6H0z"/></svg>info@yourgmail.com</div>
      <div class="row"><svg viewBox="0 0 10 10"><circle cx="5" cy="5" r="5"/></svg>www.yourwebsite.com</div>
    </div>
  </section>

  <section class="sheet card-back">
    <div class="wordmark on-dark"><span class="dot"></span>ORCHID BRIDGE</div>
  </section>

  <section class="sheet envelope-back">
    <div class="flap"><span class="mark"></span></div>
  </section>

  <section class="sheet envelope-front">
    <div class="wordmark"><span class="dot"></span>ORCHID BRIDGE</div>
    <div class="return-address">Your address, City<br>State, Zip 1234</div>
    <div class="window"></div>
  </section>

</body>
</html>
```